PAX

We need to design a power point presentation that can englobe all our company products.

This presentation has to have all the required to be used as template for future presentations.

We focus on prodcut developing for supermarkets, ( we help them with their own brand products ex. Sunny Harvest, TK, etc.)
Also we are on the marine industry, we develop ships and oil rigs for the Oil and deep water market.

Target Market(s)

Oil Companies
Supermarket companies
Retail Companies

Industry/Entity Type

It Company

Requirements
Must have
• Our Logo and company colors
Nice to have
• Something describing globalization.
Should not have
• Orange color

```html
<!DOCTYPE html>
<html lang="en">
<head>
<meta charset="utf-8">
<title>PAX – Presentation Template</title>
<link rel="stylesheet" href="https://fonts.googleapis.com/css2?family=Orbitron:wght@700;900&family=Arimo:wght@400&display=swap">
<style>
  :root {
    --brand-blue: #0f57b8;
    --brand-blue-dark: #0a3f93;
    --brand-blue-light: #2a7ad6;
    --footer-blue: #0a6cc0;
    --heading-blue: #1466b8;
    --text: #111111;
    --paper: #ffffff;
    --rule: #e4e6ea;
    --ring: #0d3fa6;
  }
  * { box-sizing: border-box; margin: 0; padding: 0; }
  html, body { width: 1200px; height: 900px; overflow: hidden; background: var(--paper); }
  .slide { position: relative; width: 1200px; height: 900px; background: var(--paper); overflow: hidden; }

  .title-band {
    position: absolute; left: 0; top: 22px; width: 1200px; height: 110px;
    background: linear-gradient(90deg, var(--brand-blue-dark) 0%, var(--brand-blue) 45%, var(--brand-blue-light) 75%, var(--brand-blue) 100%);
  }
  .project-title {
    position: absolute; left: 36px; top: 50px;
    font-family: "Orbitron", "Arial Black", sans-serif; font-weight: 900;
    font-size: 42px; letter-spacing: 2px; color: var(--paper); white-space: nowrap;
  }

  .logo-tab {
    position: absolute; left: 1008px; top: 0; width: 144px; height: 204px; z-index: 3;
    background: linear-gradient(180deg, #ffffff 0%, #f1f2f4 100%);
    border-radius: 0 0 72px 72px;
    box-shadow: 0 3px 8px rgba(0,0,0,0.25);
    display: flex; flex-direction: column; align-items: center; justify-content: center; gap: 12px;
    padding-top: 10px;
  }
  .logo-dot { width: 64px; height: 64px; border-radius: 50%; background: var(--brand-blue); }
  .logo-name {
    font-family: "Orbitron", "Arial Black", sans-serif; font-weight: 900;
    font-size: 34px; color: var(--brand-blue);
  }

  .side-rule { position: absolute; left: 11px; top: 132px; width: 2px; height: 696px; background: var(--rule); }

  .content-heading {
    position: absolute; left: 34px; top: 172px;
    font-family: "Orbitron", "Arial Black", sans-serif; font-weight: 900;
    font-size: 33px; letter-spacing: 1px; color: var(--heading-blue); white-space: nowrap;
  }
  .content-body {
    position: absolute; left: 36px; top: 226px; width: 850px;
    font-family: "Arimo", Arial, sans-serif; font-size: 21px; line-height: 36px; color: var(--text);
  }

  .bar-chart { position: absolute; left: 0; top: 480px; }

  .photo-disc {
    position: absolute; left: 992px; width: 176px; height: 176px; border-radius: 50%; z-index: 2;
    border: 7px solid var(--ring); box-shadow: 0 0 0 3px #fff, 0 2px 6px rgba(0,0,0,0.3);
  }
  .photo-disc.offshore { top: 264px; background: linear-gradient(180deg, #8fb8e0 0%, #3a6fa6 45%, #c9442c 70%, #1e4f86 100%); }
  .photo-disc.cruise { top: 476px; background: linear-gradient(180deg, #9cc4ea 0%, #e9eef3 48%, #1f5fa3 62%, #0f3d78 100%); }
  .photo-disc.refinery { top: 692px; background: linear-gradient(180deg, #38506a 0%, #1c2c3c 55%, #8a4a48 100%); }

  .footer-band { position: absolute; left: 0; top: 828px; width: 1200px; height: 72px; background: var(--footer-blue); z-index: 1; }
</style>
</head>
<body>
<main class="slide">
  <header class="title-band" role="img" aria-label="Blue band with a faint world map"></header>
  <h1 class="project-title">PROJECT TITLE HERE</h1>

  <div class="logo-tab">
    <span class="logo-dot"></span>
    <span class="logo-name">PAX</span>
  </div>

  <div class="side-rule"></div>

  <h2 class="content-heading">Content Heading Here</h2>
  <p class="content-body">Sub content here Sub content here Sub content here Sub content here Sub content here Sub content here Sub content here Sub content here Sub content here Sub content here Sub content here Sub content here</p>

  <svg class="bar-chart" width="960" height="330" viewBox="0 480 960 330" aria-label="Bar chart">
    <polygon points="40,778 58,752 948,750 945,776" fill="#d6d6d6"/>
    <rect x="40" y="776" width="905" height="14" fill="#bdbdbd"/>

    <polygon points="62,521 76,503 160,503 146,521" fill="#c8e86a"/>
    <polygon points="146,521 160,503 160,758 146,775" fill="#6f9a00"/>
    <rect x="62" y="521" width="84" height="254" fill="#a4d400"/>

    <polygon points="196,735 210,719 294,719 280,735" fill="#f0707a"/>
    <polygon points="280,735 294,719 294,760 280,775" fill="#a0000a"/>
    <rect x="196" y="735" width="84" height="40" fill="#e60012"/>

    <polygon points="316,741 330,726 414,726 400,741" fill="#80cff4"/>
    <polygon points="400,741 414,726 414,760 400,775" fill="#0a7fc0"/>
    <rect x="316" y="741" width="84" height="34" fill="#14a4ee"/>

    <polygon points="436,670 452,651 536,651 520,670" fill="#6e97d2"/>
    <polygon points="520,670 536,651 536,758 520,775" fill="#052f78"/>
    <rect x="436" y="670" width="84" height="105" fill="#0a4ca8"/>

    <polygon points="572,622 588,605 678,605 662,622" fill="#7fd8d8"/>
    <polygon points="662,622 678,605 678,758 662,775" fill="#00707a"/>
    <rect x="572" y="622" width="90" height="153" fill="#00a8b4"/>

    <polygon points="708,744 722,730 806,730 792,744" fill="#ffe27a"/>
    <polygon points="792,744 806,730 806,760 792,775" fill="#b88f00"/>
    <rect x="708" y="744" width="84" height="31" fill="#ffc900"/>

    <polygon points="832,752 846,747 930,747 914,752" fill="#7fe0a8"/>
    <polygon points="914,752 930,747 930,762 914,775" fill="#00834a"/>
    <rect x="832" y="752" width="82" height="23" fill="#00b964"/>
  </svg>

  <div class="photo-disc offshore" role="img" aria-label="Offshore supply vessels beside an oil rig at sea"></div>
  <div class="photo-disc cruise" role="img" aria-label="White cruise ship sailing on blue water"></div>
  <div class="photo-disc refinery" role="img" aria-label="Silhouette of refinery structures at dusk"></div>

  <footer class="footer-band"></footer>
</main>
</body>
</html>
```